Business cards to launch an education platform

Hi,
I am looking at having new business cards designed.
I am a startup, developing a web platform for schools and university, the education world. It's an online assessment system.
I would like a card that looks classy, and that is using the colors and the font of my logo.

I have attached:
1) my logo
2) A business card that I have designed quickly so you can have all the information required in the card, but I really don't like it.
3) The font that I am using (Lato Regular) to design my web platform
4) Some screenshots of my web platform so you can have a look at the style that I have.

Target Market(s)

Major market: Education system: Schools and university
Minor markets: Business in general

Industry/Entity Type

Business

Contact Information for Business Card

Clara Fenwick
Director

M: 0437 518 902
E: clara.fenwick@amberLoomSystems.com.au

Requirements
Must have
• The colors of my logo

```html
<!DOCTYPE html>
<html lang="en">
<head>
<meta charset="utf-8">
<title>Amber Loom Systems – Business Cards</title>
<link rel="stylesheet" href="https://fonts.googleapis.com/css2?family=Lato:wght@400;700&display=swap">
<style>
  :root {
    --backdrop: #3a3230;
    --card: #1c1c1e;
    --brand-blue: #1ea4de;
    --silver: #b9b9bb;
    --text-light: #f2f2f2;
    --divider: #5a5a5e;
  }
  * { margin: 0; padding: 0; box-sizing: border-box; }
  html, body { width: 1200px; height: 814px; overflow: hidden; }
  body {
    background: var(--backdrop);
    font-family: "Lato", Arial, sans-serif;
    position: relative;
  }
  .card {
    position: absolute;
    top: 257px;
    width: 540px;
    height: 300px;
    background: var(--card);
    border-radius: 3px;
    box-shadow: 0 10px 30px rgba(0,0,0,0.45);
  }
  .card--back { left: 40px; }
  .card--front { left: 620px; }

  /* Back */
  .back-brand {
    position: absolute;
    top: 92px; left: 0; right: 0;
    display: flex; align-items: center; justify-content: center; gap: 14px;
  }
  .back-brand__square { width: 34px; height: 34px; background: var(--silver); }
  .back-brand__name {
    font-size: 30px; font-weight: 400; color: var(--silver); letter-spacing: 1px;
  }
  .back-web {
    position: absolute;
    bottom: 48px; left: 0; right: 0;
    text-align: center;
    font-size: 15px; color: var(--silver);
  }

  /* Front */
  .front-brand {
    position: absolute;
    left: 26px; top: 0; bottom: 0; width: 200px;
    display: flex; flex-direction: column; align-items: center; justify-content: center; gap: 12px;
  }
  .front-brand__square { width: 44px; height: 44px; background: var(--brand-blue); }
  .front-brand__name {
    font-size: 19px; font-weight: 400; color: var(--brand-blue);
    text-align: center; line-height: 1.2; letter-spacing: 1px;
  }
  .front-divider {
    position: absolute;
    left: 238px; top: 44px; width: 1px; height: 212px;
    background: linear-gradient(to bottom, transparent, var(--divider) 20%, var(--divider) 80%, transparent);
  }
  .contact {
    position: absolute;
    left: 262px; top: 74px; right: 16px;
  }
  .contact__name {
    font-size: 24px; font-weight: 700; color: var(--brand-blue);
  }
  .contact__role {
    font-size: 15px; font-weight: 700; color: var(--text-light); margin-top: 2px;
  }
  .contact__list { list-style: none; margin-top: 26px; }
  .contact__item {
    display: flex; align-items: center; gap: 8px;
    font-size: 12.5px; color: var(--text-light); margin-bottom: 6px; white-space: nowrap;
  }
  .contact__icon { width: 12px; height: 12px; flex: none; }
</style>
</head>
<body>
  <section class="card card--back" aria-label="Card back">
    <div class="back-brand">
      <span class="back-brand__square"></span>
      <span class="back-brand__name">Amber Loom Systems</span>
    </div>
    <p class="back-web">www.amberLoomSystems.com.au</p>
  </section>

  <section class="card card--front" aria-label="Card front">
    <div class="front-brand">
      <span class="front-brand__square"></span>
      <span class="front-brand__name">Amber Loom<br>Systems</span>
    </div>
    <div class="front-divider"></div>
    <div class="contact">
      <h1 class="contact__name">Clara Fenwick</h1>
      <p class="contact__role">Director</p>
      <ul class="contact__list">
        <li class="contact__item">
          <svg class="contact__icon" viewBox="0 0 12 12"><rect x="3" y="0.5" width="6" height="11" rx="1" fill="none" stroke="#1ea4de" stroke-width="1.3"/><circle cx="6" cy="9.5" r="0.8" fill="#1ea4de"/></svg>
          0437 518 902
        </li>
        <li class="contact__item">
          <svg class="contact__icon" viewBox="0 0 12 12"><rect x="0.5" y="2" width="11" height="8" fill="#1ea4de"/><path d="M0.5 2 L6 6.5 L11.5 2" fill="none" stroke="#1c1c1e" stroke-width="1"/></svg>
          clara.fenwick@amberLoomSystems.com.au
        </li>
        <li class="contact__item">
          <svg class="contact__icon" viewBox="0 0 12 12"><circle cx="6" cy="6" r="5.5" fill="#1ea4de"/><path d="M0.5 6 H11.5 M6 0.5 C3 3.5 3 8.5 6 11.5 M6 0.5 C9 3.5 9 8.5 6 11.5" fill="none" stroke="#1c1c1e" stroke-width="0.8"/></svg>
          www.amberLoomSystems.com.au
        </li>
      </ul>
    </div>
  </section>
</body>
</html>
```